Counseling Practice Business Card

I need a professional looking business card incorporating my new logo that was just completed. Card needs to incorporate my name and title, description of my specialty, my address, my phone number, my fax number, my email and my website URL. I need to be able to choose design on/with different paper colors and textures.
I do not have a lot of business card ideas so I am open to anything but I want bold,sharp, clear card without additional designs other than my logo (see attached file info). I am open to different color backgrounds or paper colors including black. I do not like traditional brackets around area codes in phone number or dashes between numbers in phone number. Am open to other ways of presenting including periods between numbers as appropriate. I do not know enough to know what I like yet but I want card to coordinate and work together with my logo. My practice emphasizes natural mental health interventions so any use of color (with background paper color or the blue and green in my logo) that elicits nature is nice. In addition to black, any natural brown or wood looking background might be desirable also. Most of the offerings so far look very similar and boring.

Target Market(s)

Potential therapy clients and other professionals

Contact Information for Business Card

Card information:
Gerald M. Whitcombe, Ph.D.
Licensed Clinical Psychologist
Integrative Health Coach
4812 Marlowe Ridge Blvd SE
Suite 310
Duluth, GA 30096
(770) 415-2983 phone
(770) 581-4096 fax
drgeraldwhitcombe@quillmarsh.net
brightfernwellness.net

Font styles to use
Serif
Sans Serif
Other font styles liked:
• anything that you think looks crisp, clear and easily readable

Requirements
Must have
• Any color used should coordinate with my logo design (see attached files).
• Card should be printed horizontally so top and bottom are longest sides of rectangle.
• Background color or paper color should complement and highlight logo. Do not like a white background. black, grey, brown or any color my logo would blend well with.
Nice to have
• I would like designer to utilize color to highlight letters/name or phone-fax-web symbols.
• Bottom edge of card could be highlighted if appropriate to an idea.
Should not have
• I would NOT want the card to have a pure white background at all.
• No clear cards.
• Cards should be oriented with long sides on bottom and top, NOT sides. DO NOT LIKE THIS THIN TALL ORIENTATION.

```html
<!DOCTYPE html>
<html lang="en">
<head>
<meta charset="utf-8">
<title>Brightfern Wellness – Business Card</title>
<link href="https://fonts.googleapis.com/css2?family=Roboto:wght@400;500;700&display=swap" rel="stylesheet">
<style>
  :root {
    --backdrop: #2a2a2b;
    --card: #1c1c1d;
    --card-edge: #262627;
    --ink: #f2f2f2;
    --accent: #1f7ccc;
    --logo-ink: #c9c9cb;
  }
  html, body {
    margin: 0;
    padding: 0;
    width: 1200px;
    height: 900px;
    overflow: hidden;
    background: var(--backdrop);
    font-family: "Roboto", Arial, sans-serif;
  }
  .canvas {
    position: relative;
    width: 1200px;
    height: 900px;
  }
  .card {
    position: absolute;
    left: 290px;
    width: 620px;
    height: 354px;
    background: linear-gradient(135deg, var(--card-edge), var(--card) 60%);
    box-shadow: 0 14px 30px rgba(0,0,0,0.45);
  }
  .card-front { top: 60px; }
  .card-back { top: 486px; }

  /* Front: practice name */
  .brand {
    position: absolute;
    left: 0; right: 0; top: 0; bottom: 0;
    display: flex;
    align-items: center;
    justify-content: center;
    gap: 16px;
  }
  .brand-dot {
    width: 22px;
    height: 22px;
    border-radius: 50%;
    background: var(--logo-ink);
  }
  .brand-name {
    font-size: 44px;
    font-weight: 500;
    color: var(--logo-ink);
    letter-spacing: 0.5px;
  }

  /* Back: identity block */
  .identity {
    position: absolute;
    left: 30px;
    top: 92px;
    width: 270px;
    text-align: right;
  }
  .identity-name {
    margin: 0 0 4px;
    font-size: 22px;
    font-weight: 700;
    color: var(--accent);
    white-space: nowrap;
  }
  .identity-title {
    margin: 0;
    font-size: 16px;
    line-height: 22px;
    font-weight: 500;
    color: var(--ink);
  }
  .divider {
    position: absolute;
    left: 316px;
    top: 102px;
    width: 2px;
    height: 84px;
    background: var(--ink);
  }
  .contacts {
    position: absolute;
    left: 334px;
    top: 96px;
    margin: 0;
    padding: 0;
    list-style: none;
  }
  .contacts li {
    display: flex;
    align-items: center;
    gap: 10px;
    height: 24px;
    font-size: 15px;
    font-weight: 500;
    color: var(--ink);
    white-space: nowrap;
  }
  .contacts svg {
    width: 13px;
    height: 13px;
    flex: none;
    fill: none;
    stroke: var(--accent);
    stroke-width: 1.6;
  }
  .contacts .icon-solid { fill: var(--accent); stroke: none; }
  .web-domain { color: var(--accent); }
  .address {
    position: absolute;
    left: 60px;
    top: 258px;
    margin: 0;
    font-size: 16px;
    font-weight: 500;
    color: var(--ink);
    white-space: nowrap;
  }
</style>
</head>
<body>
<main class="canvas">
  <section class="card card-front" aria-label="Card front">
    <div class="brand">
      <span class="brand-dot"></span>
      <span class="brand-name">Brightfern Wellness</span>
    </div>
  </section>

  <section class="card card-back" aria-label="Card back">
    <div class="identity">
      <p class="identity-name">Gerald M. Whitcombe, Ph.D.</p>
      <p class="identity-title">Licensed Clinical Psychologist</p>
      <p class="identity-title">Integrative Health Coach</p>
    </div>
    <div class="divider"></div>
    <ul class="contacts">
      <li>
        <svg viewBox="0 0 16 16" aria-hidden="true"><path class="icon-solid" d="M3 1.5l3 3-1.6 1.8c.9 2 2.3 3.4 4.3 4.3L10.5 9l3 3-1.8 2.2C6.5 13.5 2.5 9.5 1.8 3.3z"/></svg>
        (770) 415-2983
      </li>
      <li>
        <svg viewBox="0 0 16 16" aria-hidden="true"><path class="icon-solid" d="M4 1h8v4H4zM1 6h14v6h-3v3H4v-3H1zM5 10v4h6v-4z"/></svg>
        (770) 581-4096
      </li>
      <li>
        <svg viewBox="0 0 16 16" aria-hidden="true"><rect x="1.5" y="3.5" width="13" height="9"/><path d="M1.5 3.5l6.5 5 6.5-5"/></svg>
        drgeraldwhitcombe@quillmarsh.net
      </li>
      <li>
        <svg viewBox="0 0 16 16" aria-hidden="true"><circle cx="8" cy="8" r="6.5"/><ellipse cx="8" cy="8" rx="2.8" ry="6.5"/><path d="M1.5 8h13"/></svg>
        <span>www.<span class="web-domain">brightfernwellness</span>.net</span>
      </li>
    </ul>
    <p class="address">4812 Marlowe Ridge Blvd SE Suite 310 Duluth, GA 30096</p>
  </section>
</main>
</body>
</html>
```